Talon Microsystems PowerPoint Master Slide Deck Design

This is a 2-phase project to design a slide deck for a semiconductor company in the Silicon Valley. The design budget will be increased with each phase.
The slide deck will need to have one version with a dark background for presentations and a second version with a white background. Otherwise, the slides will be the same. I anticipate we will need a total of 10 slides, but that number may change.
The first phase will be to design a Title and a Title and Content slide.
- The Title Slide is the first slide of the deck. It should include the presentation title, the presenter's name and date of presentation
- The Title and Content slide should include a title and content with bullet points and up to 2 additional sub-bullets
- The Title and Content slide should have a footer that includes the slide #, Talon Microsystems Confidential, and the logo. This footer will be on every slide except the Title Slide
The first two slides will serve as the format for the remaining ~8 slides:
-Header and Content Text (1, 2, 4 column)
-Header and Content Image (bar chart, pie chart, tables)
-Break
-Title only
-Closing (Talon logo only)
Our slides contain a lot of content so a clean and simple design is best.
Both phases will need to include pre-set color options for
-Text and Lines
-Shadows
-Bullets and sub-bullets (including shapes, ex. circle, slash, square, etc.)
-Bar charts, pie charts, tables
Samples of our collateral are attached. Logo files are also attached
Look and feel
Each slider illustrates characteristics of the customer's brand and the style your logo design should communicate.

```html
<!DOCTYPE html>
<html lang="en">
<head>
<meta charset="utf-8">
<title>Talon Microsystems – Slide Deck</title>
<link rel="stylesheet" href="https://fonts.googleapis.com/css2?family=Lato:wght@400;700&family=Montserrat:wght@500;600;700&display=swap">
<style>
:root{
  --canvas:#898989;
  --white:#ffffff;
  --ink:#3a3a3a;
  --muted:#6b6b6b;
  --brand:#0a3cf2;
  --brand-deep:#0a2ff5;
  --sky:#17a6fb;
  --sky-soft:#22b3ff;
  --rule:#d6dbe6;
  --check:#7a7a7a;
}
*{margin:0;padding:0;box-sizing:border-box}
html,body{width:1200px;height:4135px;overflow:hidden}
body{background:var(--canvas);position:relative;font-family:'Lato',sans-serif;color:var(--ink)}
.slide{position:absolute;left:50px;width:1098px;height:617px;background:var(--white);overflow:hidden}
.s1{top:50px}.s2{top:725px}.s3{top:1405px}.s4{top:2087px}.s5{top:2769px}.s6{top:3450px}

/* title slide */
.title-slide{background:linear-gradient(180deg,#1aa6ff 0%,#0e6cf8 45%,#0a36f6 100%);color:var(--white);text-align:center}
.title-brand{position:absolute;top:120px;left:0;right:0;display:flex;justify-content:center;align-items:center;gap:22px}
.title-brand .dot{width:54px;height:54px;border-radius:50%;border:6px solid var(--white)}
.title-brand .name{font-family:'Montserrat',sans-serif;font-weight:600;font-size:62px;letter-spacing:1px;line-height:1}
.welcome{position:absolute;top:308px;left:0;right:0;font-family:'Montserrat',sans-serif;font-weight:600;font-size:34px}
.deck-title{position:absolute;top:366px;left:0;right:0;font-family:'Montserrat',sans-serif;font-weight:600;font-size:54px;letter-spacing:.5px}
.deck-meta{position:absolute;top:460px;left:0;right:0;font-family:'Montserrat',sans-serif;font-weight:600;font-size:22px;word-spacing:2px}
.deck-meta span+span{margin-left:26px}

/* content header */
.marker{position:absolute;left:0;top:37px;width:0;height:0;border-top:24px solid transparent;border-bottom:24px solid transparent;border-left:42px solid var(--brand)}
.heading{position:absolute;left:55px;top:40px;font-family:'Montserrat',sans-serif;font-weight:700;font-size:35px;color:var(--muted);letter-spacing:.3px}
.heading em{font-style:normal;color:var(--brand);margin-left:14px}

/* columns */
.col{position:absolute;top:112px;width:446px;font-size:13.2px;line-height:29px;text-align:justify;color:var(--ink)}
.col.left{left:55px}.col.right{left:601px}
.divider{position:absolute;left:550px;top:112px;width:1px;height:400px;background:var(--rule)}
.checks{list-style:none;margin-top:8px}
.checks>li{position:relative;padding-left:22px;line-height:34px}
.checks>li::before{content:"";position:absolute;left:2px;top:11px;width:10px;height:5px;border-left:2.5px solid var(--check);border-bottom:2.5px solid var(--check);transform:rotate(-45deg)}
.subs{list-style:none;margin:4px 0 0 26px}
.subs li{position:relative;padding-left:26px;font-size:12px;line-height:25px;margin-bottom:13px}
.subs li::before{content:"";position:absolute;left:2px;top:8px;width:7px;height:7px;border-top:2.5px solid var(--sky);border-right:2.5px solid var(--sky);transform:rotate(45deg)}

/* footer */
.footer{position:absolute;left:55px;right:54px;top:556px;height:37px}
.footer .bar-left{position:absolute;left:0;top:0;width:398px;height:37px;border-radius:19px 0 0 19px;background:linear-gradient(90deg,var(--brand-deep),#0c4ff4);color:var(--white);font-size:13px;line-height:37px;padding-left:21px}
.footer .bar-right{position:absolute;right:0;top:0;width:390px;height:37px;border-radius:0 19px 19px 0;background:linear-gradient(90deg,#15a2fb,#0b63f6);color:var(--white);font-size:13px;line-height:37px;text-align:right;padding-right:12px}
.footer .mark{position:absolute;left:412px;top:0;width:166px;height:37px;display:flex;align-items:center;justify-content:center;gap:8px}
.footer .mark .dot{width:16px;height:16px;border-radius:50%;border:3px solid var(--brand)}
.footer .mark .name{font-family:'Montserrat',sans-serif;font-weight:600;font-size:24px;color:var(--brand)}

/* why choose */
.story{position:absolute;left:55px;top:118px;width:468px;font-size:13.2px;line-height:27.5px;text-align:justify}
.story p+p{margin-top:27px}
.visual{position:absolute;left:592px;top:118px;width:452px;height:362px;border:3px solid var(--sky);border-radius:8px;background:radial-gradient(ellipse at 30% 55%,#c0622a 0%,#5a3a3a 22%,#1c2d4a 48%,#0b1628 80%)}

/* chart */
.chart{position:absolute;left:30px;top:112px}
.chart text{font-family:'Lato',sans-serif;font-size:12px;fill:#333}
.chart .day{font-weight:700;font-size:12.5px}
.chart-copy{position:absolute;left:688px;top:124px;width:360px;font-size:13.2px;line-height:29px;text-align:justify}
.chart-copy p+p{margin-top:29px}

/* closing */
.closing{display:flex;align-items:center;justify-content:center;gap:34px}
.closing .dot{width:120px;height:120px;border-radius:50%;border:14px solid var(--brand)}
.closing .name{font-family:'Montserrat',sans-serif;font-weight:600;font-size:82px;line-height:1.05;color:var(--brand)}
</style>
</head>
<body>

<section class="slide s1 title-slide">
  <div class="title-brand"><span class="dot"></span><span class="name">Talon Microsystems</span></div>
  <div class="welcome">WELCOME TO</div>
  <h1 class="deck-title">TALON MICROSYSTEMS</h1>
  <div class="deck-meta"><span>FINIBUS BONORUM</span><span>DATE: 13 DEC 2023</span></div>
</section>

<section class="slide s2">
  <div class="marker"></div>
  <h2 class="heading">ABOUT TALON<em>MICROSYSTEMS</em></h2>
  <div class="col left">
    <p>Nam libero tempore, cum soluta nobis est eligendi optio cumque nihil impedit quo minus id quod maxime placeat facere possimus, omnis voluptas assumenda est, omnis dolor repellendus.</p>
    <ul class="checks">
      <li>Temporibus autem quibusdam et aut officiis debitis aut rerum</li>
      <li>Autem quibusdam et aut officiis debitis aut rerum
        <ul class="subs">
          <li>Itaque earum rerum hic tenetur a sapiente delectus, ut aut reiciendis voluptatibus maiores alias consequatur aut perferendis doloribus asperiores repellat.</li>
          <li>Tenetur a sapiente delectus, ut aut reiciendis voluptatibus maiores alias consequatur aut perferendis doloribus.</li>
          <li>At vero eos et accusamus et iusto odio dignissimos ducimus qui ent, similique sunt in culpa qui officia deserunt mollitia animi, id est laborum et dolorum fuga.</li>
        </ul>
      </li>
    </ul>
  </div>
  <div class="divider"></div>
  <div class="col right">
    <p>Libero timpedit quo minus id quod maxime placeat facere possimus, omnis voluptas assumenda est, omnis dolor repellet quo minus id quod maxime placeat facere poss ndus.</p>
    <ul class="checks">
      <li>Mporibus autem quibusdam et aut officiis debitis aut rerum</li>
      <li>Tem quibusdam et aut officiis debitis aut rerum
        <ul class="subs">
          <li>Earum rerum hic tenetur a sapiente delectus, ut aut reiciendis voluptatibus maiores alias consequatur aut perferendis doloribus asperiores repellat.</li>
          <li>Enetur a sapiente delectus, ut aut reiciendis voluptatibus maiores alias consequatur aut perferendis doloribus.</li>
          <li>Vero eos et accusamus et iusto odio dignissimos ducimus qui ent, similique sunt in culpa qui officia deserunt mollitia animi, id est laborum et dolorum fuga.</li>
        </ul>
      </li>
    </ul>
  </div>
  <div class="footer"><div class="bar-left">Talon Microsystems Confidential</div><div class="mark"><span class="dot"></span><span class="name">Talon</span></div><div class="bar-right">Page No: 02</div></div>
</section>

<section class="slide s3">
  <div class="marker"></div>
  <h2 class="heading">WHY CHOOSE<em>US</em></h2>
  <div class="story">
    <p>At vero eos et accusamus et iusto odio dignissimos ducimus qui blanditiis praesentium voluptatum deleniti atque corrupti quos dolores et quas molestias excepturi sint occaecati cupiditate non provident, similique sunt in culpa qui officia deserunt mollitia animi, id est laborum et dolorum fuga. Et harum quidem rerum facilis est et expedita distinctio. Nam libero tempore, cum soluta nobis est eligendi optio cumque nihil impedit quo minus id quod maxime placeat facere possimus, omnis voluptas assumenda est, omnis dolor repellendus. Temporibus autem quibusdam et aut officiis debitis aut rerum necessitatibus saepe eveniet ut et voluptates repudiandae sint et molestiae non recusandae.</p>
    <p>Itaque earum rerum hic tenetur a sapiente delectus, ut aut reiciendis voluptatibus maiores alias consequatur aut perferendis doloribus asperiores repellat</p>
  </div>
  <div class="visual" role="img" aria-label="Close-up photograph of glowing orange and blue circuit board traces"></div>
  <div class="footer"><div class="bar-left">Talon Microsystems Confidential</div><div class="mark"><span class="dot"></span><span class="name">Talon</span></div><div class="bar-right">Page No: 03</div></div>
</section>

<section class="slide s4">
  <div class="marker"></div>
  <h2 class="heading">OUR<em>CHART</em></h2>
  <svg class="chart" width="600" height="380" viewBox="0 0 600 380">
    <g stroke="#d4d4d4" stroke-width="1">
      <line x1="57" y1="17" x2="57" y2="351"/><line x1="133" y1="17" x2="133" y2="351"/><line x1="210" y1="17" x2="210" y2="351"/><line x1="286" y1="17" x2="286" y2="351"/><line x1="363" y1="17" x2="363" y2="351"/><line x1="439" y1="17" x2="439" y2="351"/><line x1="516" y1="17" x2="516" y2="351"/><line x1="592" y1="17" x2="592" y2="351"/>
      <line x1="57" y1="17" x2="592" y2="17"/><line x1="57" y1="351" x2="592" y2="351"/>
    </g>
    <g text-anchor="end">
      <text x="44" y="21">120</text><text x="44" y="77">100</text><text x="44" y="133">80</text><text x="44" y="188">60</text><text x="44" y="244">40</text><text x="44" y="299">20</text><text x="44" y="355">0</text>
    </g>
    <g fill="#0b2ff0">
      <rect x="73" y="73" width="14" height="278"/><rect x="149" y="101" width="14" height="250"/><rect x="226" y="212" width="14" height="139"/><rect x="302" y="73" width="14" height="278"/><rect x="379" y="73" width="14" height="278"/><rect x="455" y="184" width="14" height="167"/><rect x="532" y="212" width="14" height="139"/>
    </g>
    <g fill="#14a8fc">
      <rect x="102" y="101" width="14" height="250"/><rect x="178" y="129" width="14" height="222"/><rect x="255" y="73" width="14" height="278"/><rect x="331" y="184" width="14" height="167"/><rect x="408" y="101" width="14" height="250"/><rect x="484" y="142" width="14" height="209"/><rect x="561" y="73" width="14" height="278"/>
    </g>
    <g text-anchor="middle">
      <text x="80" y="67">100</text><text x="109" y="95">90</text>
      <text x="156" y="95">90</text><text x="185" y="123">80</text>
      <text x="233" y="206">50</text><text x="262" y="67">100</text>
      <text x="309" y="67">100</text><text x="338" y="178">60</text>
      <text x="386" y="67">100</text><text x="415" y="95">90</text>
      <text x="462" y="178">60</text><text x="491" y="136">75</text>
      <text x="539" y="206">50</text><text x="568" y="67">100</text>
    </g>
    <g text-anchor="middle" class="day">
      <text class="day" x="95" y="374">Sun</text><text class="day" x="171" y="374">Mon</text><text class="day" x="248" y="374">Tue</text><text class="day" x="324" y="374">Wed</text><text class="day" x="401" y="374">Thu</text><text class="day" x="477" y="374">Fri</text><text class="day" x="554" y="374">Sat</text>
    </g>
  </svg>
  <div class="chart-copy">
    <p>Nam libero tempore, cum soluta nobis est eligendi optio cumque nihil impedit quo minus id quod maxime placeat facere possimus, omnis voluptas assumenda et quas molestias excepturi sint occaecati cupiditate non provident, similique sunt in culpa qui officia deserunt mollitia animi, id estest, omnis dolor repellendus.</p>
    <p>Temporibus autem quibusdam et aut officiis debitis aut rerum necessitatibus saepe eveniet ut et voluptates repudiandae sint et molestiae non recusandae. Itaque earum rerum hic tenetur a sapiente delectus, ut aut reiciendis endis doloribus asperiores repellat.</p>
  </div>
  <div class="footer"><div class="bar-left">Talon Microsystems Confidential</div><div class="mark"><span class="dot"></span><span class="name">Talon</span></div><div class="bar-right">Page No: 04</div></div>
</section>

<section class="slide s5">
  <div class="marker"></div>
  <h2 class="heading">TALON<em>MICROSYSTEMS</em></h2>
  <div class="col left" style="top:124px">
    <p>At vero eos et accusamus et iusto odio dignissimos ducimus qui blanditiis praesentium voluptatum deleniti atque corrupti quos dolores et quas molestias excepturi sint occaecati cupiditate non provident, similique sunt in culpa qui officia deserunt mollitia animi, id est laborum et dolorum fuga. Et harum quidem rerum facilis est et expedita distinctio. Nam libero tempore, cum soluta nobis est eligendi optio cumque nihil impedit quo minus id quod maxime placeat facere possimus, omnis voluptas assumenda est, omnis dolor repellendus. Temporibus autem quibusdam et aut officiis debitis aut rerum necessitatibus saepe eveniet ut et voluptates repudiandae sint et molestiae non recusandae. Itaque earum rerum hic tenetur a sapiente delectus, ut aut reiciendis voluptatibus maiores alias consequatur aut perferendis doloribus asperiores repellat.</p>
  </div>
  <div class="divider" style="top:124px"></div>
  <div class="col right" style="top:124px">
    <p>Et iusto odio dignissimos ducimus qui blanditiis praesentium voluptatum deleniti atque corrupti quos dolores et quas molestias excepturi sint occaecati cupiditate non provident, similique sunt in culpa qui officia deserunt mollitia animi, id est laborum et dolorum fuga. Et harum quidem rerum facilis est et expedita distinctio. Nam libero tempore, cum soluta nobis est eligendi optio cumque nihil impedit quo minus id quod maxime placeat facere possimus, omnis voluptas assumenda est, omnis dolor repellendus. Temporibus autem quibusdam et aut officiis debitis aut rerum necessitatibus saepe eveniet ut et voluptates repuplaceat facere possimus, omnis voluptas assu diandae sint et molestiae non recusandae. Itaque earum rerum hic tenetur a sapiente delectus, ut aut reiciendis voluptatibus maiores alias consequatur aut perferendis doloribus asperiores repellat.</p>
  </div>
  <div class="footer"><div class="bar-left">Talon Microsystems Confidential</div><div class="mark"><span class="dot"></span><span class="name">Talon</span></div><div class="bar-right">Page No: 05</div></div>
</section>

<section class="slide s6 closing">
  <span class="dot"></span>
  <span class="name">Talon<br>Microsystems</span>
</section>

</body>
</html>
```